Veldmark Supplies Business Card

Professional business card that stand out to our potential customers. Front and back with clean modern design

Industry/Entity Type

Oil and gas

Contact Information for Business Card

Name, address, website , office phone and cell number

Requirements
Must have
• Editable files for each employee

```html
<!DOCTYPE html>
<html lang="en">
<head>
<meta charset="utf-8">
<title>Veldmark Supplies Business Card</title>
<link rel="stylesheet" href="https://fonts.googleapis.com/css2?family=Montserrat:wght@400;500;700;800&display=swap">
<style>
  :root {
    --brand-red: #ee2524;
    --brand-blue: #18aed3;
    --ink: #1c1c1c;
    --card: #ffffff;
    --backdrop: #e4e5e7;
  }
  * { box-sizing: border-box; margin: 0; padding: 0; }
  html, body { width: 1200px; height: 874px; overflow: hidden; }
  body {
    background: var(--backdrop);
    font-family: "Montserrat", Arial, sans-serif;
    color: var(--ink);
    display: flex;
    flex-direction: column;
    align-items: center;
    justify-content: center;
    gap: 40px;
  }
  .card {
    position: relative;
    width: 620px;
    height: 354px;
    background: var(--card);
    border-radius: 24px;
    overflow: hidden;
    box-shadow: 0 6px 18px rgba(0,0,0,.12);
  }
  .card-bands {
    position: absolute;
    left: 0; bottom: 0;
    width: 620px; height: 90px;
  }
  .brand-lockup {
    display: flex;
    align-items: center;
    gap: 12px;
  }
  .brand-mark {
    width: 22px; height: 22px;
    background: var(--brand-red);
  }
  .brand-name {
    font-weight: 800;
    color: var(--brand-red);
    letter-spacing: .06em;
    text-transform: uppercase;
  }
  /* front */
  .card-front .brand-lockup {
    position: absolute;
    left: 0; right: 0; top: 130px;
    justify-content: center;
  }
  .card-front .brand-name { font-size: 30px; }
  .card-front .brand-mark { width: 26px; height: 26px; }
  /* back */
  .card-back .brand-lockup {
    position: absolute;
    left: 40px; top: 140px;
  }
  .card-back .brand-name { font-size: 20px; }
  .contact-block {
    position: absolute;
    left: 330px; top: 56px;
    padding-left: 20px;
    border-left: 2px solid var(--brand-red);
    height: 230px;
  }
  .person-name {
    font-size: 24px;
    font-weight: 700;
    color: var(--brand-red);
    line-height: 1.1;
  }
  .person-title {
    font-size: 14px;
    font-weight: 500;
    margin-bottom: 12px;
  }
  .contact-list { list-style: none; }
  .contact-item {
    display: flex;
    align-items: center;
    gap: 8px;
    font-size: 14px;
    line-height: 23px;
  }
  .contact-icon { width: 13px; height: 13px; flex: none; }
  .address {
    font-style: normal;
    font-size: 14px;
    line-height: 19px;
    margin-top: 8px;
  }
</style>
</head>
<body>

<section class="card card-front" aria-label="Card front">
  <div class="brand-lockup">
    <span class="brand-mark"></span>
    <span class="brand-name">Veldmark Supplies</span>
  </div>
  <svg class="card-bands" viewBox="0 0 620 90" aria-hidden="true">
    <polygon points="0,0 360,70 348,90 0,90" fill="var(--brand-blue)"/>
    <polygon points="0,14 340,90 0,90" fill="var(--card)"/>
    <polygon points="368,58 620,58 620,90 352,90" fill="var(--brand-red)"/>
    <polygon points="368,58 620,58 620,72 600,90 372,62" fill="var(--card)" opacity="0"/>
  </svg>
</section>

<section class="card card-back" aria-label="Card back">
  <div class="brand-lockup">
    <span class="brand-mark"></span>
    <span class="brand-name">Veldmark Supplies</span>
  </div>

  <div class="contact-block">
    <h1 class="person-name">Tomas Reyne</h1>
    <p class="person-title">President</p>
    <ul class="contact-list">
      <li class="contact-item">
        <svg class="contact-icon" viewBox="0 0 16 16" aria-hidden="true"><path d="M2 6c0-2 3-3 6-3s6 1 6 3v1h-3V6H5v1H2z M4 8h8l1 6H3z" fill="var(--brand-blue)"/></svg>
        +1.555.210.0400 x123
      </li>
      <li class="contact-item">
        <svg class="contact-icon" viewBox="0 0 16 16" aria-hidden="true"><path d="M4 1l3 3-2 2c1 2 3 4 5 5l2-2 3 3-2 3C7 15 1 9 1 3z" fill="var(--brand-blue)"/></svg>
        +1.555.123.456
      </li>
      <li class="contact-item">
        <svg class="contact-icon" viewBox="0 0 16 16" aria-hidden="true"><rect x="1" y="3" width="14" height="10" fill="var(--brand-blue)"/><path d="M1 3l7 6 7-6" stroke="#fff" stroke-width="1.4" fill="none"/></svg>
        info@veldmarksupplies.com
      </li>
      <li class="contact-item">
        <svg class="contact-icon" viewBox="0 0 16 16" aria-hidden="true"><circle cx="8" cy="8" r="7" fill="var(--brand-blue)"/><path d="M1 8h14M8 1c-3 4-3 10 0 14M8 1c3 4 3 10 0 14" stroke="#fff" stroke-width="1" fill="none"/></svg>
        www.veldmarksupplies.com
      </li>
    </ul>
    <address class="address">48 Harbor Point Plaza<br>Lindale, NJ 07010 USA</address>
  </div>

  <svg class="card-bands" viewBox="0 0 620 90" aria-hidden="true">
    <polygon points="0,0 360,70 348,90 0,90" fill="var(--brand-blue)"/>
    <polygon points="0,14 340,90 0,90" fill="var(--card)"/>
    <polygon points="368,58 620,58 620,90 352,90" fill="var(--brand-red)"/>
  </svg>
</section>

</body>
</html>
```